Stage Design Company Business Card

We are looking to step up up our business card design for our team.

We are a Full service Design and Consultation company for Stage and TV with an emphasis in Theatrical Lighting.

We like our materials to be clean and modern with solid colors free of patterns and gradients. Our brand consists of 4 primary colors Purple, Black, Grey, and White. Provided is our Word Mark as well as our Symbol Logo.

We would like our cards to leave an impression beyond the information, show our attention to design and detail, and make our marks an easily recognized feature (together or apart) for our clients.

We need a warm approachable comfortable feel for some clients, and a professional flair for the board member type clients.

Attached are our brand elements, and our existing cards to give a sense of our style and a glipse at the information we provide on our cards.

Target Market(s)

broad client base from church leaders to high school teachers and architects.

Industry/Entity Type

Business

Contact Information for Business Card

We format our phone number with periods not parenthesis or dashes. Information will be edited for each of our team members, and team member specific cards are not part of this scope, but rather a template so to speak.

Font styles to use
Sans Serif

Colors
6b449b
ffffff
000000
333333
aaaaaa

Requirements
Must have
• Wordmark and logo mark present (does not need to exist on the same side of card)
• Brand Colors,
• Name, Phone, Email, Address.
• Unique choices that make someone stop and take a second look
Nice to have
• It would be nice to somehow convey what we DO, as our brand name does not lend itself to this, outside of an obvious tagline though.....
• social media if not crowded. all of our handles match (instagram, twitter, facebook)
Should not have
• "clipart"

```html
<!DOCTYPE html>
<html lang="en">
<head>
<meta charset="utf-8">
<title>Marlow Stageworks – Business Card</title>
<link href="https://fonts.googleapis.com/css2?family=Questrial&display=swap" rel="stylesheet">
<style>
  :root {
    --backdrop: #000000;
    --card: #333333;
    --card-edge: #444444;
    --ink: #ffffff;
    --grey: #aaaaaa;
    --purple: #6b449b;
  }
  * { margin: 0; padding: 0; box-sizing: border-box; }
  html, body {
    width: 1200px;
    height: 1076px;
    overflow: hidden;
    background: var(--backdrop);
    font-family: "Questrial", sans-serif;
  }
  .canvas {
    position: relative;
    width: 1200px;
    height: 1076px;
  }
  .card {
    position: absolute;
    width: 750px;
    height: 432px;
    background: var(--card);
    border: 1px solid var(--card-edge);
    box-shadow: 0 18px 40px rgba(0, 0, 0, 0.6);
    overflow: hidden;
  }

  /* Front side */
  .card--front {
    left: 100px;
    top: 50px;
  }
  .brand {
    position: absolute;
    left: 0;
    right: 0;
    top: 110px;
    display: flex;
    flex-direction: column;
    align-items: center;
  }
  .brand-dot {
    width: 74px;
    height: 74px;
    border-radius: 50%;
    background: var(--purple);
    margin-bottom: 34px;
  }
  .brand-name {
    color: var(--ink);
    font-size: 44px;
    letter-spacing: 22px;
    padding-left: 22px;
    line-height: 1;
  }
  .brand-tagline {
    margin-top: 18px;
    color: var(--grey);
    font-size: 11px;
    letter-spacing: 9px;
    padding-left: 9px;
  }

  /* Back side */
  .card--back {
    left: 315px;
    top: 511px;
  }
  .back-feature {
    position: absolute;
    left: 0;
    top: 0;
    width: 360px;
    height: 100%;
  }
  .contact {
    position: absolute;
    left: 380px;
    right: 40px;
    top: 78px;
    color: var(--ink);
    text-align: center;
  }
  .contact-name {
    font-size: 32px;
    letter-spacing: 3px;
    font-weight: 400;
    margin-bottom: 54px;
  }
  .contact-phone {
    font-size: 29px;
    letter-spacing: 0.5px;
    margin-bottom: 34px;
  }
  .contact-email {
    font-size: 23px;
    letter-spacing: 1px;
    margin-bottom: 50px;
  }
  .contact-address {
    font-size: 24px;
    letter-spacing: 3px;
    line-height: 1.25;
    font-style: normal;
  }
</style>
</head>
<body>
<main class="canvas">

  <section class="card card--front" aria-label="Card front">
    <div class="brand">
      <span class="brand-dot" aria-hidden="true"></span>
      <span class="brand-name">MARLOW</span>
      <span class="brand-tagline">STAGEWORKS</span>
    </div>
  </section>

  <section class="card card--back" aria-label="Card back">
    <svg class="back-feature" viewBox="0 0 360 432" preserveAspectRatio="none"
         role="img" aria-label="Large brand symbol decoration bleeding off the left edge">
      <rect width="360" height="432" fill="#6b449b"/>
    </svg>
    <div class="contact">
      <h1 class="contact-name">OWEN R MARLOW</h1>
      <p class="contact-phone">555.014.2290</p>
      <p class="contact-email">owen@marlow-s.com</p>
      <address class="contact-address">12 N ELM ST<br>LARKFIELD, AZ 85000</address>
    </div>
  </section>

</main>
</body>
</html>
```